New Business Card Design Project

We require a business card design for Vexalund, a newly established Indian company.
Our focus is on the development, manufacturing, and export of a diverse array of pharmaceutical products on a global scale. The card should convey a professional appearance, as our primary markets are in Africa, China, and Southeast Asian nations.
We envision a two-sided business card, with the reverse side dedicated to a logo set against a solid color or an elegantly designed pattern. The corners should be rounded. We would appreciate seeing both horizontal and vertical design options. We trust the designer to utilize their expertise in creating this design.

The content for the business card is included in the attached Word file.

Target Market(s)

Our primary markets are in Africa, China, and Southeast Asian, Latin America, Maldives, Sri Lanka

Industry/Entity Type

Pharmaceutical Manufacturing and Export

Contact Information for Business Card

Colors

Designer to choose colors to be used in the design.

Requirements
Must have
• The reverse side of the business card features solely the logo along with the tagline, "Care Across Borders."
Should not have
• The logo should not exceed two instances, encompassing both the front and back sides of the card.

```html
<!DOCTYPE html>
<html lang="en">
<head>
<meta charset="utf-8">
<title>Vexalund Business Card</title>
<link href="https://fonts.googleapis.com/css2?family=Open+Sans:wght@400;600;700&family=Poppins:wght@400;600&display=swap" rel="stylesheet">
<style>
  :root {
    --stage: #222222;
    --card: #1c1c1c;
    --blue: #2ea8e0;
    --coral: #f06552;
    --white: #ffffff;
    --text-sans: "Open Sans", Arial, sans-serif;
    --brand-sans: "Poppins", Arial, sans-serif;
  }
  * { margin: 0; padding: 0; box-sizing: border-box; }
  html, body { width: 1200px; height: 711px; overflow: hidden; background: var(--stage); }
  .stage { position: relative; width: 1200px; height: 711px; }

  .card {
    position: absolute;
    top: 207px;
    width: 518px;
    height: 296px;
    border-radius: 20px;
    background: var(--card);
    overflow: hidden;
    box-shadow: 0 10px 22px rgba(0, 0, 0, 0.55);
  }
  .card--front { left: 76px; }
  .card--back { left: 605px; }

  .decor-panel { position: absolute; top: 0; height: 100%; }
  .card--front .decor-panel {
    left: 345px; width: 173px;
    background: linear-gradient(160deg, var(--white) 0%, var(--blue) 55%, #2594c8 100%);
  }
  .card--back .decor-panel {
    left: 0; width: 172px;
    background: linear-gradient(200deg, var(--white) 0%, var(--coral) 55%, #d9543f 100%);
  }

  .brand {
    position: absolute;
    display: flex;
    align-items: center;
    gap: 8px;
  }
  .card--front .brand { left: 18px; top: 100px; }
  .card--back .brand { left: 421px; top: 232px; transform: translateX(-50%); }
  .brand-name {
    font-family: var(--brand-sans);
    font-weight: 600;
    font-size: 32px;
    line-height: 1;
    color: var(--blue);
    white-space: nowrap;
  }
  .brand-dot {
    width: 12px; height: 12px;
    border-radius: 50%;
    background: var(--coral);
    flex: none;
  }

  .tagline {
    position: absolute;
    left: 421px; top: 269px;
    transform: translateX(-50%);
    font-family: var(--brand-sans);
    font-size: 13.5px;
    color: var(--blue);
    white-space: nowrap;
  }

  .name-bar {
    position: absolute;
    left: 0; top: 151px;
    width: 11px; height: 36px;
    background: var(--coral);
  }
  .person-name {
    position: absolute;
    left: 19px; top: 148px;
    font-family: var(--text-sans);
    font-size: 22px;
    line-height: 1.2;
    white-space: nowrap;
  }
  .person-name .first { color: var(--blue); font-weight: 700; }
  .person-name .last { color: var(--coral); font-weight: 400; }
  .person-role {
    position: absolute;
    left: 19px; top: 173px;
    font-family: var(--text-sans);
    font-size: 12px;
    color: var(--white);
  }
  .address {
    position: absolute;
    left: 19px; top: 196px;
    font-family: var(--text-sans);
    font-size: 11.5px;
    line-height: 15px;
    color: var(--blue);
    font-style: normal;
  }
  .contact-list { position: absolute; left: 19px; top: 234px; list-style: none; }
  .contact-item {
    display: flex;
    align-items: center;
    height: 15.5px;
    font-family: var(--text-sans);
    font-size: 11.5px;
    color: var(--white);
    white-space: nowrap;
  }
  .contact-icon { width: 11px; height: 11px; margin-right: 6px; flex: none; }
</style>
</head>
<body>
<main class="stage">
  <section class="card card--front" aria-label="Card front">
    <div class="brand">
      <span class="brand-name">Vexalund</span>
      <span class="brand-dot"></span>
    </div>

    <span class="name-bar"></span>
    <h1 class="person-name"><span class="first">Arvind</span> <span class="last">K. Shelke</span></h1>
    <p class="person-role">CEO</p>
    <address class="address">14, Nilgiri Colony,<br>Wardha, 442001, India</address>
    <ul class="contact-list">
      <li class="contact-item">
        <svg class="contact-icon" viewBox="0 0 12 12"><rect x="3" y="0.8" width="6" height="10.4" rx="1" fill="none" stroke="#f06552" stroke-width="1.2"/></svg>
        +91 98765 01234
      </li>
      <li class="contact-item">
        <svg class="contact-icon" viewBox="0 0 12 12"><circle cx="6" cy="6" r="5.5" fill="#2ea8e0"/><path d="M0.5 6h11M6 0.5c-2.5 3-2.5 8 0 11M6 0.5c2.5 3 2.5 8 0 11" stroke="#1c1c1c" stroke-width="0.7" fill="none"/></svg>
        www.vexalund.com
      </li>
      <li class="contact-item">
        <svg class="contact-icon" viewBox="0 0 12 12"><rect x="0.5" y="3" width="11" height="8" fill="#f06552"/><path d="M0.5 3l5.5 4.5 5.5-4.5" stroke="#1c1c1c" stroke-width="0.8" fill="none"/></svg>
        ashelke@vexalund.com
      </li>
    </ul>

    <div class="decor-panel" role="img" aria-label="Large brand symbol decoration, blue half"></div>
  </section>

  <section class="card card--back" aria-label="Card back">
    <div class="decor-panel" role="img" aria-label="Large brand symbol decoration, coral half"></div>
    <div class="brand">
      <span class="brand-name">Vexalund</span>
    </div>
    <p class="tagline">Care Across Borders.</p>
  </section>
</main>
</body>
</html>
```